Business Card Design for Occupational Medicine Start Up Company

We need to design a professional business card. We are a healthcare company providing occupational medicine services to blue collar industries. We are professional, efficient and high quality service providers.

Target Market(s)

Blue Collar Industry: Shipbuilding, Ports, Trucking Companies; The Executives and Safety Officers for these companies

Industry/Entity Type

Healthcare

Contact Information for Business Card

Logo, Name, Title, Email, Phone

Other font styles liked:
• Please match our Brand Guide

Requirements
Must have
• Our Company Colors and Logo

```html
<!DOCTYPE html>
<html lang="en">
<head>
<meta charset="utf-8">
<title>Crewline Clinics – Business Card</title>
<link rel="stylesheet" href="https://fonts.googleapis.com/css2?family=Montserrat:wght@400;500;600;700&display=swap">
<style>
  :root {
    --stage: #2a2a2a;
    --navy: #2e3277;
    --card-blue: #31337a;
    --sky: #2e9bd6;
    --amber: #f0a93a;
    --paper: #f6f6f4;
    --white: #ffffff;
    --ink: #2e3277;
  }
  * { margin: 0; padding: 0; box-sizing: border-box; }
  html, body {
    width: 1200px; height: 1200px; overflow: hidden;
    background: var(--stage);
    font-family: "Montserrat", sans-serif;
  }
  .canvas { position: relative; width: 1200px; height: 1200px; }

  .card {
    position: absolute;
    width: 594px; height: 348px;
    border-radius: 18px;
    overflow: hidden;
  }

  /* Back side */
  .card-back { left: 298px; top: 200px; background: var(--card-blue); }
  .card-back .brand-mark {
    position: absolute; left: 0; right: 0; top: 140px;
    display: flex; align-items: center; justify-content: center; gap: 14px;
    color: #6a6fd8; font-weight: 600; font-size: 34px; letter-spacing: 1px;
  }
  .card-back .brand-mark .dot {
    width: 26px; height: 26px; border-radius: 50%; background: #6a6fd8;
  }
  .card-back .site {
    position: absolute; left: 0; right: 0; top: 300px;
    text-align: center; font-size: 15px; font-weight: 500; letter-spacing: 1.5px;
    color: var(--white);
  }
  .site .accent-sky { color: var(--sky); }
  .site .accent-amber { color: var(--amber); }

  /* Front side */
  .card-front { left: 292px; top: 637px; background: var(--paper); }
  .wordmark {
    position: absolute; left: 24px; top: 40px;
    color: var(--navy); font-weight: 700; font-size: 24px; letter-spacing: 0.5px;
    line-height: 1;
  }
  .wordmark-circle {
    position: absolute; left: 350px; top: 6px;
    width: 290px; height: 290px; border-radius: 50%;
    background: var(--sky); opacity: 0.12;
  }
  .person-name {
    position: absolute; left: 24px; top: 138px;
    color: var(--sky); font-weight: 600; font-size: 24px; letter-spacing: 0.5px;
  }
  .person-title {
    position: absolute; left: 24px; top: 168px;
    color: var(--ink); font-size: 15px;
  }
  .address {
    position: absolute; left: 24px; top: 210px;
    color: var(--ink); font-size: 15px; line-height: 21px;
  }
  .contacts {
    position: absolute; left: 24px; top: 261px;
    list-style: none; color: var(--ink); font-size: 15px;
  }
  .contacts li { display: flex; align-items: center; gap: 14px; height: 21px; }
  .contacts svg { width: 13px; height: 13px; flex: none; }
</style>
</head>
<body>
<main class="canvas">

  <section class="card card-back" aria-label="Card back">
    <div class="brand-mark"><span class="dot"></span><span>Crewline Clinics</span></div>
    <p class="site">www.<span class="accent-sky">crewline</span><span class="accent-amber">clinics</span>.com</p>
  </section>

  <section class="card card-front" aria-label="Card front">
    <div class="wordmark-circle"></div>
    <p class="wordmark">CREWLINE CLINICS</p>
    <h1 class="person-name">DANA HOLLOWAY</h1>
    <p class="person-title">Senior Doctor</p>
    <p class="address">48 Harbor Lane, Suite 210<br>Bayview, State 54321</p>
    <ul class="contacts">
      <li>
        <svg viewBox="0 0 14 14" aria-hidden="true"><path fill="#2e9bd6" d="M1 4c0-2 2-3 6-3s6 1 6 3v1h-3V4H4v1H1zM3 6h8l2 6H1z"/></svg>
        555-214-0388
      </li>
      <li>
        <svg viewBox="0 0 14 14" aria-hidden="true"><rect x="1" y="3" width="12" height="8" fill="#2e3277"/><path d="M1 3l6 5 6-5" stroke="#f6f6f4" stroke-width="1.2" fill="none"/></svg>
        hello@crewlineclinics.com
      </li>
      <li>
        <svg viewBox="0 0 14 14" aria-hidden="true"><circle cx="7" cy="7" r="6" fill="#f0a93a"/><path d="M1 7h12M7 1v12M3 3.5c2 1.2 6 1.2 8 0M3 10.5c2-1.2 6-1.2 8 0" stroke="#f6f6f4" stroke-width="0.8" fill="none"/></svg>
        www.crewlineclinics.com
      </li>
    </ul>
  </section>

</main>
</body>
</html>
```